Restaurant Menu New Design

Hello Designers,

Blue Fern is a casual family oriented dine-in restaurant, we serve American Italian dishes like Pizza, Pasta, and Sandwiches.

We are excited about adding some new delicious dishes and recipes to our menu. And we are looking for a talented and creative designer to design it.

The menu is a 12 page black leather book, page size is:
6.5" X 11.69" (16.51 cm X 29.69 cm)

Below is the scope of work and requirements:

1) Design a completely all new, creative, and beautiful menu, including cover page, blue fern oven intro. page, interior pages, and kids menu page.

2) Design a take out edition of the menu. It will be exactly the same as the dine-in menu, but with the addition of a back cover page with info such as contacts, social media, location map, etc…

3) Files are required in Adobe Illustrator format. Layers should be organized, all text should be editable, and all the food pictures easy to change.

4) This is a two language menu, so you are required to make space in the design for a second language. The easiest way to do that is have every item listed in English twice, then I will edit the second text with Illustrator.

5) In your initial design submission, the minimum you are required to submit are these 4 pages:
– Cover page
– Typical interior menu page
– Kids menu page
– Take-out menu back cover page

If your initial design is selected, then you are required to submit all remaining pages to complete the project.

In the link below, you will find:
1) Logo
2) New menu text in Excel
3) Food images (will take some time to upload)
4) The old dine-in and take out menu designs

https://www.filevaultra.com/sh/kq7tmwzabe3pxd/BBBrTnpLk41QaWmZpQ8V2X7Jd?dl=0

Thank you for stopping by and reading this brief. I hope you like this project and enjoy designing our new menu. Please let me know if you have any questions.

Cheers!

Project Deadline Extended
Reason: We have decided to extend the deadline due to the low number of submissions which was much lower than the expected submissions we were give by Brief Harbor.

```html
<!DOCTYPE html>
<html lang="en">
<head>
<meta charset="utf-8">
<title>Blue Fern – Pizza Menu Page</title>
<link rel="stylesheet" href="https://fonts.googleapis.com/css2?family=Lato:wght@400;700&family=Noto+Naskh+Arabic:wght@400;700&display=swap">
<style>
  :root {
    --page-bg: #3a3a3c;
    --ink: #ffffff;
    --ink-soft: #a4a4a6;
    --rule: #e6e6e6;
    --ornament: rgba(255,255,255,0.10);
    --crust: #c98a45;
    --sauce: #a4402a;
    --pan: #1e1e1f;
  }
  * { margin: 0; padding: 0; box-sizing: border-box; }
  html, body { width: 668px; height: 1200px; overflow: hidden; background: var(--page-bg); }
  .menu-page {
    position: relative; width: 668px; height: 1200px;
    background: var(--page-bg); color: var(--ink);
    font-family: "Lato", "Noto Naskh Arabic", sans-serif;
  }
  .abs { position: absolute; }
  .section-title { font-size: 21px; font-weight: 400; letter-spacing: 0.5px; text-align: center; width: 120px; }
  .rule { position: absolute; height: 2px; background: var(--rule); }
  .frame-v { position: absolute; width: 2px; background: var(--rule); }
  .ornament { position: absolute; border-radius: 10px; background: var(--ornament); }
  .photo { position: absolute; }
  .photo-beef { background: radial-gradient(circle at 50% 50%, #b8733b 0%, #8a4a2a 48%, var(--pan) 60%, #5a3e2a 100%); }
  .photo-pepperoni { background: linear-gradient(135deg, #d9a86a 0%, var(--sauce) 40%, #e8c48a 65%, var(--pan) 100%); }
  .photo-greek { background: radial-gradient(circle at 48% 50%, #d8964c 0%, #c5763a 45%, var(--pan) 62%, #2a1f1a 100%); }
  .dish { position: absolute; text-align: center; }
  .dish-name { font-size: 14.5px; font-weight: 700; line-height: 17px; }
  .dish-name .ar { font-family: "Noto Naskh Arabic", serif; font-weight: 400; }
  .dish-desc { color: var(--ink-soft); font-size: 10px; line-height: 12px; margin-top: 12px; }
  .dish-desc-ar { color: var(--ink-soft); font-family: "Noto Naskh Arabic", serif; font-size: 10px; line-height: 12.5px; margin-top: 10px; direction: rtl; }
  .col-left { left: 40px; width: 280px; }
  .col-right { left: 368px; width: 260px; }
  .col-veg-left { left: 62px; width: 260px; }
</style>
</head>
<body>
<main class="menu-page">

  <!-- header -->
  <h1 class="abs section-title" style="left:122px; top:54px;">PIZZA</h1>
  <h1 class="abs section-title" style="left:438px; top:54px;">PIZZA</h1>
  <div class="rule" style="left:4px; top:86px; width:220px;"></div>
  <div class="rule" style="left:424px; top:86px; width:244px;"></div>
  <div class="ornament" role="img" aria-label="Line drawing of a serving cloche" style="left:310px; top:56px; width:72px; height:48px;"></div>
  <div class="ornament" role="img" aria-label="Line drawings of tomato, beet and pepper" style="left:136px; top:100px; width:96px; height:28px;"></div>
  <div class="ornament" role="img" aria-label="Line drawings of peas, lemon and mushroom" style="left:428px; top:100px; width:132px; height:28px;"></div>

  <!-- row 1 photos -->
  <div class="rule" style="left:48px; top:145px; width:184px;"></div>
  <div class="frame-v" style="left:48px; top:145px; height:178px;"></div>
  <div class="frame-v" style="left:314px; top:264px; height:60px;"></div>
  <div class="photo photo-beef" role="img" aria-label="Photo of a spicy beef pizza in a pan" style="left:67px; top:166px; width:238px; height:158px;"></div>

  <div class="rule" style="left:376px; top:153px; width:88px;"></div>
  <div class="frame-v" style="left:376px; top:152px; height:88px;"></div>
  <div class="frame-v" style="left:636px; top:192px; height:140px;"></div>
  <div class="rule" style="left:552px; top:330px; width:86px;"></div>
  <div class="photo photo-pepperoni" role="img" aria-label="Photo of a pepperoni pizza slice with stretching cheese" style="left:386px; top:166px; width:238px; height:158px;"></div>

  <div class="ornament" role="img" aria-label="Line drawing of a pizza spatula" style="left:320px; top:172px; width:36px; height:76px;"></div>
  <div class="ornament" role="img" aria-label="Line drawing of an onion" style="left:328px; top:264px; width:44px; height:72px;"></div>

  <!-- row 1 dishes -->
  <section class="dish col-left" style="top:346px;">
    <h2 class="dish-name">SPICEY BEEF | <span class="ar">اللحم الحارق</span></h2>
    <p class="dish-desc">Spicy ground beef, pepperoni, white onions,<br>bell peppers, and cilantro&nbsp; 37</p>
    <p class="dish-desc-ar">لحم مفروم مبهر بالفلفل الحارق، بيبروني، بصل<br>أبيض، فلفل رومي، كزبرة&nbsp; 37</p>
  </section>
  <section class="dish col-right" style="top:346px;">
    <h2 class="dish-name">PEPPERONI | <span class="ar">بيبروني</span></h2>
    <p class="dish-desc">Pepperoni slices, mozzarella,<br>cheese,tomato</p>
    <p class="dish-desc-ar">شرائح البيبروني وجبنة الموزاريلا<br>وصلصة الطماطم&nbsp; 34</p>
  </section>
  <div class="ornament" role="img" aria-label="Line drawings of chili peppers and a tomato" style="left:312px; top:360px; width:84px; height:72px;"></div>

  <!-- divider -->
  <div class="rule" style="left:4px; top:472px; width:664px;"></div>
  <div class="ornament" role="img" aria-label="Line drawing of a rolling pin" style="left:252px; top:458px; width:188px; height:28px; border-radius:14px;"></div>

  <!-- row 2 -->
  <div class="photo photo-greek" role="img" aria-label="Photo of a sliced chicken pizza with red peppers" style="left:67px; top:506px; width:237px; height:157px;"></div>
  <div class="frame-v" style="left:314px; top:552px; height:122px;"></div>
  <div class="ornament" role="img" aria-label="Line drawings of a mushroom and an eggplant" style="left:328px; top:524px; width:64px; height:100px;"></div>
  <section class="dish col-right" style="top:498px;">
    <h2 class="dish-name">GREEK | <span class="ar">بيتزا يونانية</span></h2>
    <p class="dish-desc" style="margin-top:10px;">Tomatos, kalamata olives,greenbell<br>peppers, spinach,tomato sauce,<br>mozzarella&amp;crumbledfeta</p>
    <p class="dish-desc-ar">قطع الطماطم، زيتون، فلفل رومي أخضر،<br>سبانخ، صلصة الطماطم، جبنة فيتا وجبنة<br>الموزاريلا&nbsp; 35</p>
  </section>

  <div class="rule" style="left:346px; top:674px; width:99px;"></div>
  <div class="rule" style="left:540px; top:674px; width:100px;"></div>

  <!-- row 3 -->
  <section class="dish col-left" style="top:698px;">
    <h2 class="dish-name">CAHSHEW CHICKEN TERIYAKI |<br><span class="ar">تيرياكي الدجاج والكاشو</span></h2>
    <p class="dish-desc" style="margin-top:22px;">Teriyaki chicken strips, sesame, crunchy<br>cashews, red bell peppers, spring onions,<br>mozzarella cheese&nbsp; 37</p>
    <p class="dish-desc-ar">دجاج بصوص التيرياكي و السمسم، كاشو مقرمش،<br>فلفل رومي أحمر، بصل أخضر والموزاريلا الساخنة&nbsp; 37</p>
  </section>
  <section class="dish col-right" style="top:698px;">
    <h2 class="dish-name">BEEF TERIYAKI PIZZAC51 |<br><span class="ar">بيتزا تيرياكي لحم</span></h2>
    <p class="dish-desc" style="margin-top:22px;">Thin slices of Teriyaki beef, sesame, red bell<br>peppers,spring onions, mozzarella cheese<br>39</p>
    <p class="dish-desc-ar">شرائح اللحم الخفيفة بصوص التيرياكي و<br>السمسم، فلفل رومي أحمر، بصل أخضر<br>والموزاريلا الساخنة</p>
  </section>
  <div class="ornament" role="img" aria-label="Line drawing of a carrot" style="left:316px; top:696px; width:60px; height:60px;"></div>
  <div class="ornament" role="img" aria-label="Line drawing of a beet" style="left:312px; top:772px; width:44px; height:48px;"></div>

  <div class="rule" style="left:52px; top:862px; width:98px;"></div>
  <div class="rule" style="left:298px; top:862px; width:90px;"></div>
  <div class="rule" style="left:540px; top:862px; width:100px;"></div>

  <!-- veggie grid -->
  <section class="dish col-veg-left" style="top:900px;">
    <h2 class="dish-name">VEGGIE | <span class="ar">خضروات</span></h2>
    <p class="dish-desc" style="margin-top:13px;">Mushrooms, green<br>peppers,onions, black olives&nbsp; 32</p>
    <p class="dish-desc-ar">بصل أخضر، فلفل رومي، فطر<br>وزيتون&nbsp; 32</p>
  </section>
  <section class="dish col-right" style="top:898px;">
    <h2 class="dish-name">VEGGIE | <span class="ar">خضروات</span></h2>
    <p class="dish-desc" style="margin-top:13px;">Mushrooms, green<br>peppers,onions, black olives&nbsp; 32</p>
    <p class="dish-desc-ar">بصل أخضر، فلفل رومي، فطر<br>وزيتون&nbsp; 32</p>
  </section>
  <section class="dish col-veg-left" style="top:1028px;">
    <h2 class="dish-name">VEGGIE | <span class="ar">خضروات</span></h2>
    <p class="dish-desc" style="margin-top:13px;">Mushrooms, green<br>peppers,onions, black olives&nbsp; 32</p>
    <p class="dish-desc-ar">بصل أخضر، فلفل رومي، فطر<br>وزيتون&nbsp; 32</p>
  </section>
  <section class="dish col-right" style="top:1024px;">
    <h2 class="dish-name">VEGGIE | <span class="ar">خضروات</span></h2>
    <p class="dish-desc" style="margin-top:13px;">Mushrooms, green<br>peppers,onions, black olives&nbsp; 32</p>
    <p class="dish-desc-ar">بصل أخضر، فلفل رومي، فطر<br>وزيتون&nbsp; 32</p>
  </section>
  <div class="ornament" role="img" aria-label="Line drawings of a pear, an apple and a plum" style="left:316px; top:892px; width:76px; height:136px;"></div>

  <!-- bottom divider -->
  <div class="rule" style="left:4px; top:1150px; width:664px;"></div>
  <div class="ornament" role="img" aria-label="Line drawing of a rolling pin" style="left:252px; top:1136px; width:188px; height:28px; border-radius:14px;"></div>

</main>
</body>
</html>
```